Podiatry (services) Business Card

I need a business design for a New Podiatry Service.
the Podiatry services will include all aspects of podiatry including;
general podiatry for all ages
corns and callus treatment
Ingrown toenails & nail surgery
Forefoot, arch and heel pain
Gait analysis
Sports Podiatry and Orthotics
Paediatric Assessments
Diabetes Foot Assessment

I would like the back of the card to have space for next appointment day and time.

I would like a nice design that is simple yet catchy. I don't like cluttered business cards. I like things to be simple yet stand out because of the finer details.

I like the colours blue and white but I'm open to other designs that have different colours.

Business

Bluewren Podiatry (Business name)

Marisol Tenbury - Podiatrist
M.Pod.P., B.Hlth. Sci, MFLsoc

Address: 58 Coleby St, Marrowdale North Vic, 3164
Phone: (03) 9416 2738
Fax: (03) 9523 4178

```html
<!DOCTYPE html>
<html lang="en">
<head>
<meta charset="utf-8">
<title>Bluewren Podiatry – Business Card</title>
<link href="https://fonts.googleapis.com/css2?family=Source+Sans+3:wght@400;600&display=swap" rel="stylesheet">
<style>
  :root {
    --backdrop: #3b3430;
    --card-black: #121212;
    --card-white: #ffffff;
    --brand-blue: #1a7fd0;
    --text-light: #f2f2f2;
  }
  * { box-sizing: border-box; margin: 0; padding: 0; }
  html, body {
    width: 1200px; height: 844px; overflow: hidden;
    background: var(--backdrop);
    font-family: "Source Sans 3", "Helvetica Neue", Arial, sans-serif;
  }
  .card-set { position: relative; width: 1200px; height: 844px; }
  .card {
    position: absolute; top: 268px;
    width: 540px; height: 308px;
    background: var(--card-black);
    border-radius: 4px;
    overflow: hidden;
    box-shadow: 0 10px 28px rgba(0,0,0,.45);
  }
  .card--front { left: 40px; }
  .card--back { left: 620px; }

  /* Front */
  .brand {
    position: absolute; top: 62px; left: 0; right: 0;
    display: flex; align-items: center; justify-content: center; gap: 14px;
  }
  .brand__dot {
    width: 34px; height: 34px; border-radius: 50%;
    background: var(--brand-blue);
  }
  .brand__name {
    color: var(--brand-blue); font-weight: 400;
    font-size: 34px; letter-spacing: 2px; text-transform: uppercase;
  }
  .practitioner {
    position: absolute; left: 36px; top: 168px;
    color: var(--text-light); font-size: 15px; line-height: 1.3;
  }
  .practitioner__name { color: var(--brand-blue); font-weight: 600; font-size: 18px; }
  .practitioner__address { margin-top: 16px; }
  .contact {
    position: absolute; right: 30px; top: 200px;
    color: var(--text-light); font-size: 15px; line-height: 1.45;
    text-align: right;
  }
  .contact__row { display: flex; align-items: center; justify-content: flex-end; gap: 6px; }
  .contact__icon { width: 13px; height: 13px; fill: var(--brand-blue); }

  /* Back */
  .back-curve { position: absolute; inset: 0; }
  .services {
    position: absolute; left: 30px; top: 30px;
    list-style: none; color: var(--text-light);
    font-size: 14px; line-height: 19.5px;
  }
  .services li { display: flex; align-items: center; gap: 8px; }
  .services li::before {
    content: ""; width: 6px; height: 6px; border-radius: 50%;
    background: var(--brand-blue); flex: none;
  }
  .back-brand {
    position: absolute; right: 28px; top: 34px;
    display: flex; align-items: center; gap: 8px;
  }
  .back-brand__dot { width: 22px; height: 22px; border-radius: 50%; background: var(--brand-blue); }
  .back-brand__name { color: var(--brand-blue); font-size: 16px; letter-spacing: 1px; text-transform: uppercase; }
  .appointment {
    position: absolute; left: 30px; right: 30px; top: 208px;
    color: var(--brand-blue); font-size: 14px; font-weight: 600;
  }
  .appointment__title { text-align: center; font-size: 16px; margin-bottom: 10px; padding-left: 120px; }
  .appointment__row { display: flex; align-items: baseline; gap: 6px; margin-bottom: 12px; }
  .appointment__line { flex: 1; border-bottom: 1.5px dotted var(--brand-blue); }
</style>
</head>
<body>
<main class="card-set">

  <section class="card card--front" aria-label="Card front">
    <div class="brand">
      <span class="brand__dot"></span>
      <span class="brand__name">Bluewren Podiatry</span>
    </div>
    <div class="practitioner">
      <p><span class="practitioner__name">Marisol Tenbury</span> - Podiatrist</p>
      <p>M.Pod.P., B.Hlth. Sci, MFLsoc</p>
      <p class="practitioner__address">58 Coleby St, Marrowdale<br>North Vic, 3164</p>
    </div>
    <div class="contact">
      <p class="contact__row">(03) 9416 2738
        <svg class="contact__icon" viewBox="0 0 24 24" aria-hidden="true"><path d="M6.6 10.8a15.1 15.1 0 0 0 6.6 6.6l2.2-2.2a1 1 0 0 1 1-.25 11.4 11.4 0 0 0 3.6.6 1 1 0 0 1 1 1V20a1 1 0 0 1-1 1A17 17 0 0 1 3 4a1 1 0 0 1 1-1h3.5a1 1 0 0 1 1 1c0 1.25.2 2.45.6 3.6a1 1 0 0 1-.25 1z"/></svg>
      </p>
      <p class="contact__row">(03) 9523 4178
        <svg class="contact__icon" viewBox="0 0 24 24" aria-hidden="true"><path d="M7 3h8l2 2v4H7zM4 10h16a1 1 0 0 1 1 1v8a1 1 0 0 1-1 1H4a1 1 0 0 1-1-1v-8a1 1 0 0 1 1-1zm3 6v2h10v-2z"/></svg>
      </p>
    </div>
  </section>

  <section class="card card--back" aria-label="Card back">
    <svg class="back-curve" viewBox="0 0 540 308" preserveAspectRatio="none" aria-hidden="true">
      <path d="M0 212 Q300 205 540 112 L540 308 L0 308 Z" fill="var(--card-white)"/>
    </svg>
    <ul class="services">
      <li>General podiatry for all ages</li>
      <li>Corns and callus treatment</li>
      <li>Ingrown toenails &amp; nail surgery</li>
      <li>Forefoot, arch and heel pain</li>
      <li>Gait analysis</li>
      <li>Sports Podiatry and Orthotics</li>
      <li>Paediatric Assessments</li>
      <li>Diabetes Foot Assessment</li>
    </ul>
    <div class="back-brand">
      <span class="back-brand__dot"></span>
      <span class="back-brand__name">Bluewren Podiatry</span>
    </div>
    <div class="appointment">
      <p class="appointment__title">Appointment</p>
      <div class="appointment__row">
        <span class="appointment__line" style="flex:0.6"></span>
        <span>Date:</span><span class="appointment__line"></span>
        <span>Time:</span><span class="appointment__line"></span>
      </div>
      <div class="appointment__row">
        <span>Name:</span><span class="appointment__line"></span>
      </div>
    </div>
  </section>

</main>
</body>
</html>
```